Roofing Contractor business card redesign

I want to redesign my business card with a fresh, eye catching concept

Target Market(s)

Residential Roofing Clients, potential employees, and subcontractors.

Industry/Entity Type

Business

Colors

Designer to choose colors to be used in the design.

Requirements
Nice to have
• I just want something that's more pleasing to the eye. You can use a combination of either / or of my logos.

```html
<!DOCTYPE html>
<html lang="en">
<head>
<meta charset="utf-8">
<title>Brightway Contractors – Business Card</title>
<link rel="stylesheet" href="https://fonts.googleapis.com/css2?family=Oswald:wght@500;600&family=Work+Sans:wght@300;400&display=swap">
<style>
  :root {
    --orange: #f3841f;
    --brown: #4a1410;
    --white: #ffffff;
    --stage: #2e2e2e;
  }
  * { box-sizing: border-box; margin: 0; padding: 0; }
  html, body { width: 1200px; height: 930px; overflow: hidden; background: var(--stage); }
  .canvas { position: relative; width: 1200px; height: 930px; }

  .card {
    position: absolute;
    left: 278px;
    width: 644px;
    height: 368px;
    border-radius: 24px;
    overflow: hidden;
    background: var(--orange);
  }
  .card--front { top: 76px; }
  .card--back { top: 486px; }

  .card__curves { position: absolute; inset: 0; width: 644px; height: 368px; }

  .front-brand {
    position: absolute;
    left: 58px;
    top: 150px;
    display: flex;
    align-items: center;
    gap: 10px;
  }
  .brand-dot {
    width: 34px; height: 34px;
    border-radius: 50%;
    background: var(--orange);
    flex: none;
  }
  .brand-name {
    font-family: "Oswald", sans-serif;
    font-weight: 600;
    color: var(--brown);
    line-height: 1.05;
  }
  .front-brand .brand-name { font-size: 26px; }

  .contact {
    position: absolute;
    right: 38px;
    top: 82px;
    text-align: right;
    color: var(--white);
    font-family: "Work Sans", sans-serif;
    font-weight: 300;
    font-size: 16px;
    line-height: 20px;
  }
  .contact__name {
    font-family: "Oswald", sans-serif;
    font-weight: 500;
    font-size: 29px;
    line-height: 34px;
    letter-spacing: 0.5px;
    text-transform: uppercase;
  }
  .contact__block { margin-top: 10px; }
  .contact__line { display: flex; justify-content: flex-end; align-items: center; gap: 8px; }
  .contact__line svg { width: 12px; height: 12px; flex: none; }

  .back-brand {
    position: absolute;
    inset: 0;
    display: flex;
    align-items: center;
    justify-content: center;
    gap: 16px;
  }
  .back-brand .brand-dot { width: 70px; height: 70px; background: var(--brown); }
  .back-brand .brand-name { font-size: 46px; }
</style>
</head>
<body>
<main class="canvas">

  <section class="card card--front">
    <svg class="card__curves" viewBox="0 0 644 368" aria-hidden="true">
      <path d="M0 0 L306 0 C365 70 352 230 200 368 L0 368 Z" fill="var(--brown)"/>
      <path d="M0 0 L266 0 C340 60 360 210 186 368 L0 368 Z" fill="var(--white)"/>
    </svg>

    <div class="front-brand">
      <span class="brand-dot"></span>
      <span class="brand-name">Brightway<br>Contractors, Inc.</span>
    </div>

    <div class="contact">
      <p class="contact__name">Dale Whitcomb</p>
      <p>Certified Roof Inspector</p>
      <p>Licensed Property Adjuster</p>
      <div class="contact__block">
        <p>4820 Elm Ridge Road</p>
        <p>Suite 110 Dallas, TX 75230</p>
      </div>
      <div class="contact__block">
        <p class="contact__line">(555) 210-4800
          <svg viewBox="0 0 12 12"><path d="M2.5 1 L4.5 1 L5.2 3.6 L4 4.6 C4.6 6 5.8 7.3 7.3 8 L8.3 6.8 L11 7.5 L11 9.5 C11 10.3 10.3 11 9.5 11 C5 11 1 7 1 2.5 C1 1.7 1.7 1 2.5 1 Z" fill="var(--brown)"/></svg>
        </p>
        <p class="contact__line">(555) 318-2694
          <svg viewBox="0 0 12 12"><rect x="3" y="0.8" width="6" height="10.4" rx="1.2" fill="none" stroke="var(--brown)" stroke-width="1.4"/><circle cx="6" cy="9.2" r="0.7" fill="var(--brown)"/></svg>
        </p>
        <p class="contact__line">dale@brightwaytx.com
          <svg viewBox="0 0 12 12"><rect x="0.8" y="2.5" width="10.4" height="7" rx="0.8" fill="none" stroke="var(--brown)" stroke-width="1.2"/><path d="M1 3 L6 6.6 L11 3" fill="none" stroke="var(--brown)" stroke-width="1.2"/></svg>
        </p>
      </div>
    </div>
  </section>

  <section class="card card--back">
    <div class="back-brand">
      <span class="brand-dot"></span>
      <span class="brand-name">Brightway<br>Contractors, Inc.</span>
    </div>
  </section>

</main>
</body>
</html>
```